Innovative WordPress for a non-profit organization dedicated to providing healthcare to the less for

Bright Harbor Aid is a small non-profit organization. BHA's core mission is to provide free medical and dental care to the less fortunate. Aside from providing healthcare, BHA also helps build infrastructure such as orphanage, cancer centers, water wells and small homes for the homeless. As a non-profit, BHA has been sponsoring various social programs to help those in need. From building infrastructure to health care and most recently micro-finance, the BHA team is helping to GIve Back to the community at person at a time.

BHA is growing and needs help to restructure for the future. The corporate website design is the first step in a new branding strategy for the company.

BHA current website is divided into three specific target areas:
1. Mission: This area is dedicated to provide information about medical and dental mission hosted by BHA.

2. Infrastructure. This area is dedicated to provide information about infrastructure programs supported and completed by the BHA team. The projects includes orphanage, cancer centers. water wells, micro-finance, small homes for the homeless...etc.

3. Special Projects. This area is used to showcase specific short term projects which might come up.

Aside from the specific three target area, BHA also needs a NEWS area where news about BHA can be published.

Please put your thinking cape on and help produce the next generation WordPress template for Bright Harbor Aid. Your design will great enhance the level of volunteers recruited and also increase the level of help that BHA can provide for other.

For a quick glance at the BHA website today, please visit http://www.brightharboraid-example.org. The BHA team is looking for a fresh design.

Thank you very much for taking the time to help BHA advance its mission of helping those in need.

Reason: Seeking more variety in design. Design needs to have a donate button, sponsors area, news, welcome message, 3 primary functions (mission, infrastructure, and specials projects). The BHA logo is available. Please note, you have the option to NOT use the colors associated with BHA logo. Thank you for helping with designing the new site.

Non-Profit

Requirements
Must have
• 1. Donate Now button.
2. Primary focus areas: MISSION / INFRASTRUCTURE / SPECIAL PROJECTS
3. News & Events
4. Welcome Message area
5. Sponsors area - place to add sponsor logos

Nice to have
• 1. Photo of the Month: Used to show a specific photo to represent events or functions completed by the BHA team.

Please show sample of one level down. For example, what does the page look like when I click the MISSION link.

```html
<!DOCTYPE html>
<html lang="en">
<head>
<meta charset="utf-8">
<title>Bright Harbor Aid — Serving The Disadvantage Community</title>
<link rel="stylesheet" href="https://fonts.googleapis.com/css2?family=Arimo:wght@400;700&display=swap">
<style>
:root{
  --red:#e52420;
  --red-dark:#b8120f;
  --green:#1f9a48;
  --green-dark:#137a35;
  --ink:#222;
  --text:#333;
  --muted:#666;
  --page:#f1f1f1;
  --band-top:#5a5a5a;
  --band-bottom:#8e8e8e;
  --footer:#2a2a2a;
  --footer-bar:#0d0d0d;
  --line:#d6d6d6;
  --blue-rule:#2a5aa8;
  --yellow:#f2d21b;
  --sponsor:#e4e4e4;
}
*{box-sizing:border-box;margin:0;padding:0}
html,body{width:933px;height:1200px;overflow:hidden}
body{position:relative;background:var(--page);font-family:"Arimo",Arial,sans-serif;color:var(--text)}
.abs{position:absolute}

/* header */
.header{left:0;top:0;width:933px;height:88px;background:#fff}
.hero-band{left:0;top:88px;width:933px;height:382px;background:linear-gradient(var(--band-top),var(--band-bottom) 70%,#d9d9d9)}
.logo-tab{left:141px;top:25px;width:201px;height:90px;background:linear-gradient(#fff,#eee);border-radius:8px 8px 0 0;box-shadow:0 2px 6px rgba(0,0,0,.35);display:flex;align-items:center;justify-content:center;gap:8px}
.logo-mark{width:26px;height:26px;border-radius:50%;background:var(--green)}
.logo-name{font-weight:700;font-size:17px;line-height:18px;color:var(--ink)}
.tagline{left:440px;top:14px;width:358px;text-align:right;font-size:20px;color:#555}
.search{left:574px;top:48px;display:flex;gap:6px}
.search-input{width:149px;height:20px;border:1px solid #bbb;background:#fff}
.search-btn{width:68px;height:20px;background:var(--green);color:#fff;font-size:11px;display:flex;align-items:center;justify-content:center;border:1px solid var(--green-dark)}
.donate-btn{left:470px;top:48px;width:92px;height:20px;background:var(--red);border:1px solid var(--red-dark);color:#fff;font-size:11px;font-weight:700;display:flex;align-items:center;justify-content:center}

/* navigation */
.main-nav{left:126px;top:110px;width:683px;height:31px;background:linear-gradient(#ff4a3d,var(--red) 50%,var(--red-dark));border-radius:6px 6px 0 0;display:flex}
.main-nav a{flex:1;color:#fff;text-decoration:none;font-size:13px;display:flex;align-items:center;justify-content:center;border-right:1px solid rgba(255,255,255,.35)}
.main-nav a:last-child{border-right:0}

/* slider */
.slide-photo{left:126px;top:141px;width:683px;height:300px;background:linear-gradient(160deg,#6f7e86,#c9c2b8 45%,#e7e1da 70%,#8a8f86)}
.slide-caption{left:126px;top:350px;width:683px;height:91px;background:rgba(40,40,40,.45);text-align:center;color:#fff}
.slide-caption h2{font-size:20px;line-height:20px;margin-top:8px;text-shadow:0 1px 2px rgba(0,0,0,.6)}
.slide-caption p{font-size:12px;margin-top:8px}
.slide-arrow{top:281px;width:22px;height:40px;background:rgba(90,90,90,.85);color:#fff;display:flex;align-items:center;justify-content:center}
.slide-dock{left:126px;top:441px;width:683px;height:28px;background:linear-gradient(#fafafa,#dcdcdc);border-radius:0 0 40px 40px/0 0 12px 12px}
.slide-dots{left:416px;top:433px;width:104px;height:24px;background:linear-gradient(#fff,#ddd);border-radius:4px;box-shadow:0 1px 3px rgba(0,0,0,.3);display:flex;align-items:center;justify-content:center;gap:3px}
.dot{width:13px;height:13px;border-radius:50%;background:radial-gradient(circle at 40% 35%,#eee,#999)}
.dot.active{background:radial-gradient(circle at 40% 35%,#ff7a6c,var(--red-dark))}

/* content */
.content{left:126px;top:497px;width:683px;height:565px;background:#fff;border:1px solid var(--line);border-radius:4px}
.welcome-title{left:126px;top:510px;width:683px;text-align:center;font-size:33px;font-weight:400;color:var(--ink)}
.welcome-title span{color:var(--green)}
.welcome-text{left:141px;top:558px;width:651px;font-size:8.4px;line-height:11px;color:var(--text)}
.welcome-text p{margin-bottom:8px}

.sponsors{left:141px;top:712px;width:651px;height:24px;display:flex;align-items:center;gap:10px}
.sponsors-label{font-size:10px;font-weight:700;color:var(--ink);width:78px}
.sponsor-slot{flex:1;height:22px;background:var(--sponsor);border:1px solid var(--line);border-radius:3px}

.panel{border:1px solid var(--line);background:#fff}
.panel-head{height:28px;border-bottom:2px solid var(--blue-rule);display:flex;align-items:center;justify-content:space-between;padding:0 10px;font-size:13px;color:var(--ink)}
.panel-head a{font-size:8.5px;color:var(--red);font-weight:700;text-decoration:underline}
.news{left:141px;top:745px;width:412px;height:113px}
.about{left:570px;top:745px;width:221px;height:113px}
.news-items{display:flex;gap:18px;padding:12px 12px}
.news-item{display:flex;gap:8px;width:180px}
.thumb{width:42px;height:48px;flex:none;border:1px solid #ccc}
.thumb.news-photo{background:linear-gradient(#cfe3ef,#9fb8c6)}
.thumb.about-photo{width:54px;height:56px;background:linear-gradient(#a8a89a,#6e6a5c)}
.news-item b{display:block;font-size:8.4px;color:var(--ink)}
.small{font-size:8px;line-height:10px;color:var(--muted)}
.about-body{display:flex;gap:8px;padding:12px 10px 0}
.read-more{font-size:8px;color:var(--red);font-weight:700;text-align:right;padding-right:10px}

/* focus areas */
.focus-tray{left:141px;top:868px;width:651px;height:187px;background:linear-gradient(#d8d8d8,#bdbdbd);border-radius:4px}
.focus-card{top:874px;width:204px;height:176px;background:#fff;box-shadow:0 1px 4px rgba(0,0,0,.35);text-align:center}
.focus-card h3{font-size:16px;font-weight:400;color:var(--ink);margin-top:8px;letter-spacing:.2px}
.focus-photo{width:186px;height:68px;margin:5px auto 0}
.focus-card p{text-align:left;padding:7px 9px 0;font-size:8.4px;line-height:10.3px;color:var(--text);height:50px;overflow:hidden}
.btn-green{display:inline-flex;align-items:center;justify-content:center;width:68px;height:15px;margin-top:5px;background:var(--green);color:#fff;font-size:8.5px;border:1px solid var(--green-dark)}

/* footer */
.footer{left:0;top:1062px;width:933px;height:138px;background:linear-gradient(#555,var(--footer) 25%)}
.footer-nav{left:126px;top:1068px;width:683px;height:48px;background:var(--footer-bar);border-radius:0 0 20px 20px;display:flex;align-items:flex-end;padding-bottom:8px}
.footer-nav a{flex:1;color:#fff;text-decoration:none;font-size:12px;text-align:center}
.footer-logo{left:182px;top:1130px;display:flex;align-items:center;gap:5px}
.footer-logo .logo-mark{width:16px;height:16px}
.footer-logo span{color:#fff;font-weight:700;font-size:11px;line-height:11px}
.follow{left:400px;top:1123px;width:130px;text-align:center;color:#fff;font-size:9.5px}
.social{display:flex;gap:6px;justify-content:center;margin-top:5px}
.social i{width:16px;height:16px;border-radius:50%;background:#6f8fbf}
.newsletter-note{left:604px;top:1124px;font-size:9.5px;color:#fff}
.newsletter{left:543px;top:1142px;display:flex;align-items:center;gap:6px}
.newsletter label{color:var(--yellow);font-size:11px}
.newsletter .field{width:136px;height:16px;background:#fff;font-size:7.5px;color:#777;padding:4px}
.newsletter .submit{width:48px;height:16px;background:var(--red);color:#fff;font-size:9px;font-weight:700;display:flex;align-items:center;justify-content:center}
.copyright{left:290px;top:1172px;width:354px;height:28px;background:var(--footer-bar);border-radius:14px 14px 0 0;color:#fff;font-size:10px;text-align:center;padding-top:8px}
</style>
</head>
<body>

<header class="abs header"></header>
<div class="abs hero-band"></div>

<div class="abs logo-tab">
  <span class="logo-mark"></span>
  <span class="logo-name">Bright Harbor<br>Aid</span>
</div>
<div class="abs tagline">Serving The Disadvantage Community</div>
<a class="abs donate-btn" href="#">Donate Now</a>
<div class="abs search"><div class="search-input"></div><div class="search-btn">Search</div></div>

<nav class="abs main-nav">
  <a href="#">Home</a><a href="#">About Us</a><a href="#">Mission</a><a href="#">Special Projects</a><a href="#">Infrastructure</a><a href="#">Events</a>
</nav>

<div class="abs slide-photo" role="img" aria-label="Photo of smiling volunteers in white coats at a dental clinic"></div>
<div class="abs slide-caption">
  <h2>Dr. Mara Linden (far right) working with the volunteers<br>at a BHA dental clinic</h2>
  <p>Dr. Mara Linden mentoring group of volunteers who will be future dentist at the BHA Dental</p>
</div>
<div class="abs slide-arrow" style="left:126px">&#10094;</div>
<div class="abs slide-arrow" style="left:787px">&#10095;</div>
<div class="abs slide-dock"></div>
<div class="abs slide-dots"><i class="dot active"></i><i class="dot"></i><i class="dot"></i><i class="dot"></i><i class="dot"></i></div>

<main class="abs content"></main>
<h1 class="abs welcome-title">Welcome To <span>bha-example.org</span></h1>
<div class="abs welcome-text">
  <p>Bright Harbor Aid (BHA) is non profit - 501 C (3) organization dedicated to providing health-care, Human services, and educational assistance to underprivileged communities. we work in collaboration with various groups and non-governmental organizations (NGOs). to deliver humanitarian goods, services and relief to impoverished regions. The team is comprised of professionals with a broad spectrum of experiences. the combined mission trips of our team span across north America, South Africa, South America, and South East Asia, bringing a variety of general and specialized disciplines to each region.</p>
  <p>The BHA team initial medical mission project was Phnom Penh, Cambodia in March 2005. The mission team provided care to over 2.500 patients. In november 2005, The BHA Team collaborated with Coastal Care Alliance (CCA) to bring a medical, Dental and public Health mission to Da Nang, Vietnam. This medical mission provided treatments to over 2.700 students from first to fifth grades. The team served students five elementary schools, delivering over 1.500 dental procedures and 500 medical examinations. The team also successfully introduced public health program including basic and oral higienic training for all students and their parents. Such training is intended to help reduce the risk of disease and infection over time.</p>
  <p>From the experiences of the first two mission trips, Bright Harbor Aid (BHA) was formally incorporated in August 2006. As a formally incorporated and qualified non-profit organization, BHA is better positioned to provide assistance to those in need. From 2006 to present, The BHA team has grown and diversified exponentially. BHA's primary mission is focused toward providing health care services to the disadvantage community. Building infrastucture such as orphanage, cancer centers and other special programs.</p>
</div>

<section class="abs sponsors" aria-label="Sponsors">
  <span class="sponsors-label">Our Sponsors</span>
  <span class="sponsor-slot"></span><span class="sponsor-slot"></span><span class="sponsor-slot"></span><span class="sponsor-slot"></span><span class="sponsor-slot"></span><span class="sponsor-slot"></span>
</section>

<section class="abs panel news">
  <div class="panel-head">Latest News &amp; Events <a href="#">View All</a></div>
  <div class="news-items">
    <div class="news-item">
      <div class="thumb news-photo" role="img" aria-label="News photo of a dental check-up"></div>
      <div><b>Lorem ipsum dolor sit amet</b><div class="small">March, 22th 2014</div><div class="small">Lorem ipsum dolor sit amet,consec teteur adipiscing elit. set diem...</div></div>
    </div>
    <div class="news-item">
      <div class="thumb news-photo" role="img" aria-label="News photo of a patient visit"></div>
      <div><b>Lorem ipsum dolor sit amet</b><div class="small">March, 22th 2014</div><div class="small">Lorem ipsum dolor sit amet,consec teteur adipiscing elit. set diem...</div></div>
    </div>
  </div>
</section>

<section class="abs panel about">
  <div class="panel-head">About Us</div>
  <div class="about-body">
    <div class="thumb about-photo" role="img" aria-label="Photo of the team members together"></div>
    <div class="small">Lorem ipsum dolor sit amet,consec teteur adipiscing elit. set diem nonu my inservalls gravida neque. Nulla gravida vestibulum nim veniam.</div>
  </div>
  <div class="read-more">read more</div>
</section>

<div class="abs focus-tray"></div>
<article class="abs focus-card" style="left:150px">
  <h3>MISSION</h3>
  <div class="focus-photo" role="img" aria-label="Photo of a mission team beside a clinic services sign" style="background:linear-gradient(#8c9a6d,#5e6e45)"></div>
  <p>Through the years, BHA has hosted numerous different type of dental/ medical missions. Most recently, the BHA team hosted a free dental clinic at the ...</p>
  <span class="btn-green">Read more</span>
</article>
<article class="abs focus-card" style="left:365px">
  <h3>INFRASTRUCTURE</h3>
  <div class="focus-photo" role="img" aria-label="Photo of a cancer center building" style="background:linear-gradient(#b9c7d3,#a17a63)"></div>
  <p>Linh Mercy Cancer Center - Riverside House from hosting various dental and medical missions through out the year, the BHA team also engages in infrastructure ...</p>
  <span class="btn-green">Read more</span>
</article>
<article class="abs focus-card" style="left:580px">
  <h3>SPECIAL PROJECTS</h3>
  <div class="focus-photo" role="img" aria-label="Group photo of volunteers in green shirts" style="background:linear-gradient(#7ea06a,#5f8a3e)"></div>
  <p>Through the years, BHA has hosted numerous different type of dental/ medical missions. Most recently, the BHA team hosted a free dental clinic at the ...</p>
  <span class="btn-green">Read more</span>
</article>

<footer class="abs footer"></footer>
<nav class="abs footer-nav">
  <a href="#">Home</a><a href="#">About Us</a><a href="#">Mission</a><a href="#">Special Projects</a><a href="#">Infrastructure</a><a href="#">Events</a>
</nav>
<div class="abs footer-logo"><span class="logo-mark"></span><span>Bright Harbor<br>Aid</span></div>
<div class="abs follow">FOLLOW US ON :
  <div class="social"><i></i><i></i><i></i><i></i><i></i></div>
</div>
<div class="abs newsletter-note">Sign Up and start receive our newsletter weekly</div>
<div class="abs newsletter"><label>Newsletter</label><div class="field">Your email address</div><div class="submit">SUBMIT</div></div>
<div class="abs copyright">Copyright &copy; 2014, bha-example.org. All rights reserved.</div>

</body>
</html>
```